Vellisant - Quality health delivered at your door

Vellisant offers home and Community Based Services for adults who wish to continue live independently in their communities. We increase accessibility to health care, reduce health care delivery gap, reduce mortality and morbidity, reduce health while promoting healthy living in the comfort of our patients communities or homes.

We provide on site services and deliver high quality healthcare at your door. Our experienced physicians coordinate care with our certified nurse practitioners and provide chronic care management, physical therapy, rehabilitation and medications management.

Target Market(s)

Older population living in independent living facilities

Industry/Entity Type

Health Care

Contact Information for Business Card

Vellisant

Number of Pages Required

4 page

Font styles to use
Sans Serif

Colors

Designer to choose colors to be used in the design.

```html
<!DOCTYPE html>
<html lang="en">
<head>
<meta charset="utf-8">
<title>Vellisant – Quality health delivered at your door</title>
<link href="https://fonts.googleapis.com/css2?family=Lato:wght@400;700&family=Lora:wght@400;700&display=swap" rel="stylesheet">
<style>
:root{
  --orange:#f39a12;
  --orange-dark:#d9820a;
  --green-dark:#2b3f0b;
  --green:#4a6a1a;
  --green-light:#79a441;
  --ink:#1a2a05;
  --grey:#6b6b6b;
  --line:#e3e3e3;
  --white:#fff;
}
*{box-sizing:border-box;margin:0;padding:0}
html,body{width:712px;height:1200px;overflow:hidden;background:var(--white);font-family:"Lato",sans-serif;color:var(--ink)}
.page{position:relative;width:712px;height:1200px}
.abs{position:absolute}
.btn{position:absolute;display:flex;align-items:center;justify-content:center;background:linear-gradient(#f7a823,var(--orange-dark));border-radius:18px;font-family:"Lato",sans-serif;font-weight:700;box-shadow:0 2px 0 #c0700a}
/* header */
.brand{position:absolute;left:46px;top:12px;width:112px;text-align:center}
.brand-mark{width:56px;height:56px;border-radius:50%;background:var(--orange);margin:0 auto 6px;border:4px solid var(--green-dark)}
.brand-name{font-family:"Lato",sans-serif;font-size:16px;color:var(--green-dark)}
.phone-icon{left:344px;top:20px;width:24px;height:24px;border:1px solid #999;border-radius:50%}
.phone-text{left:376px;top:25px;font-size:10px;color:#999}
.phone-text b{font-size:13px;color:#111;font-weight:700}
.contact{left:530px;top:17px;width:136px;height:30px;color:var(--white);font-size:11.5px}
.nav{position:absolute;left:198px;top:68px;display:flex;gap:9px;font-family:"Lora",serif;font-size:8.5px;color:#444}
.nav span{padding:0 2px}
.nav .active{border-bottom:2px solid var(--green-dark);padding-bottom:19px}
/* hero */
.hero{left:0;top:99px;width:712px;height:303px;background:linear-gradient(90deg,#fafafa 0%,#eeeeee 45%,#e6dcd8 70%,#dcd4cf 100%)}
.hero-photo{left:330px;top:99px;width:382px;height:303px;background:linear-gradient(90deg,rgba(240,236,232,0),#e2cfc8 50%,#d8c6be)}
.kicker{left:47px;top:187px;font-family:"Lora",serif;font-weight:700;font-size:20px;color:var(--orange)}
.headline{left:47px;top:212px;font-size:28.5px;font-weight:700;color:var(--ink)}
.lede{left:47px;top:257px;width:320px;font-size:12.5px;line-height:15.5px;color:#111}
.learn{left:46px;top:304px;width:117px;height:31px;color:var(--ink);font-size:12.5px}
.arrow{top:238px;font-size:24px;color:#111}
/* intro */
.intro{left:0;top:402px;width:712px;height:183px;background:linear-gradient(var(--green),var(--green-dark));color:var(--white);text-align:center}
.intro-ring{position:absolute;left:280px;top:14px;width:152px;height:152px;border-radius:50%;border:6px solid rgba(255,255,255,.05)}
.section-title{font-family:"Lora",serif;font-weight:700;font-size:29px;color:var(--orange);text-align:center;width:712px;left:0}
.intro p{position:absolute;left:80px;width:552px;font-size:9.8px;line-height:13.7px}
/* services */
.card{position:absolute;top:657px;width:150px;height:184px;border:1px solid var(--line);background:var(--white);text-align:center}
.card.featured{background:#efefef;border-color:#efefef}
.card-photo{width:100%;height:92px}
.card h3{font-family:"Lora",serif;font-weight:400;font-size:11.2px;line-height:12.5px;color:var(--ink);margin:16px 8px 6px}
.card.featured h3{color:var(--orange)}
.card p{font-size:8.4px;line-height:11.3px;color:var(--grey);margin:0 10px}
.viewall{left:297px;top:854px;width:117px;height:30px;color:var(--ink);font-size:12.5px}
/* newsletter */
.newsletter{left:0;top:915px;width:712px;height:99px;background:linear-gradient(90deg,var(--green) 0%,var(--green-light) 60%,#6f9b3a 100%)}
.news-label{left:44px;top:946px;font-family:"Lora",serif;font-weight:700;font-size:28px;color:var(--white)}
.news-input{left:269px;top:948px;width:307px;height:34px;background:var(--white);border-radius:17px;font-size:8.5px;color:#999;padding:13px 0 0 17px}
.submit{left:580px;top:950px;width:86px;height:30px;color:var(--ink);font-size:12.5px}
/* footer */
.foot-brand{left:0;width:712px;top:1047px;text-align:center}
.foot-brand .brand-mark{width:54px;height:54px;margin-bottom:4px}
.social{position:absolute;top:1134px;width:31px;height:31px;border-radius:50%;border:2px solid var(--green-dark)}
.social.on{background:radial-gradient(circle at 40% 35%,#f7a823,#b8700a);border-color:transparent}
.copy{left:0;width:712px;top:1176px;text-align:center;font-size:8.5px;color:#555}
.copy b{font-family:"Lora",serif;color:var(--ink)}
</style>
</head>
<body>
<div class="page">
  <!-- header -->
  <div class="brand"><div class="brand-mark"></div><div class="brand-name">VELLISANT</div></div>
  <div class="abs phone-icon">
    <svg width="22" height="22" viewBox="0 0 24 24"><path d="M8 6c1 0 2 3 1.5 3.5l-1 1c.8 2 2.3 3.5 4 4.5l1-1c.5-.5 3.5.5 3.5 1.5 0 1.5-1.5 2.5-3 2-4-1.3-7.2-4.5-8-8.5C5.7 7.5 6.5 6 8 6z" fill="var(--orange)"/></svg>
  </div>
  <div class="abs phone-text">Call Us Now : <b>555-0142-768</b></div>
  <div class="btn contact">CONTACT US NOW</div>
  <nav class="nav"><span class="active">Home</span><span>Assisted Living</span><span>Skilled Nursing</span><span>Independent Living</span><span>Services</span><span>Respite Care</span><span>Rehabilitation</span><span>Kelvra</span></nav>

  <!-- hero -->
  <div class="abs hero"></div>
  <div class="abs hero-photo" role="img" aria-label="Photo of a smiling nurse caring for an elderly woman"></div>
  <div class="abs kicker">THE LOVE AND CARE</div>
  <div class="abs headline">FOR YOUR GOLDEN YEARS</div>
  <p class="abs lede">Lorem Ipsum is simply dummy text of the printing and typesetting industry. Lorem Ipsum has been the</p>
  <div class="btn learn">LEARN MORE</div>
  <div class="abs arrow" style="left:17px">&#10094;</div>
  <div class="abs arrow" style="left:682px">&#10095;</div>

  <!-- intro -->
  <section class="abs intro">
    <div class="intro-ring"></div>
    <h2 class="abs section-title" style="top:27px">STAY HOME</h2>
    <p style="top:72px">Vellisant offers home and Community Based Services for adults who wish to continue to live independently in the comfort of their communities.</p>
    <p style="top:113px">We provide on site services and deliver high quality healthcare at your door. &nbsp;Our experienced physicians coordinate care with our certified nurse practitioners and provide chronic care management, physical therapy, rehabilitation and medications management.</p>
  </section>

  <!-- services -->
  <h2 class="abs section-title" style="top:610px">SERVICES</h2>
  <article class="card featured" style="left:46px">
    <div class="card-photo" role="img" aria-label="Photo of a caregiver helping an elderly man with a walker" style="background:linear-gradient(135deg,#c9a67a,#8a8a78)"></div>
    <h3>Comprehensive primary care services</h3>
    <p>Orvane offers important business benefits and resources to help get the job done.</p>
  </article>
  <article class="card" style="left:202px">
    <div class="card-photo" role="img" aria-label="Photo of a caregiver with an elderly woman in a wheelchair outdoors" style="background:linear-gradient(135deg,#a57a5c,#4f6b3a)"></div>
    <h3>Coordination of speciality care</h3>
    <p>Orvane offers important business benefits and resources to help get the job done.</p>
  </article>
  <article class="card" style="left:359px">
    <div class="card-photo" role="img" aria-label="Photo of a nurse with an elderly woman" style="background:linear-gradient(135deg,#7fa9c8,#e6e6ea)"></div>
    <h3>Asthma, Diabetes mellitus, Heart</h3>
    <p>Orvane offers important business benefits and resources to help get the job done.</p>
  </article>
  <article class="card" style="left:516px">
    <div class="card-photo" role="img" aria-label="Photo of a doctor and family reviewing results with an elderly woman" style="background:linear-gradient(135deg,#d8d0c4,#6a6a5e)"></div>
    <h3>Alzheimer’s dementia</h3>
    <p>Orvane offers important business benefits and resources to help get the job done on time and under budget.</p>
  </article>
  <div class="btn viewall">VIEW ALL</div>

  <!-- newsletter -->
  <div class="abs newsletter"></div>
  <div class="abs news-label">NEWSLETTER :</div>
  <div class="abs news-input">Enter Email*</div>
  <div class="btn submit">SUBMIT</div>

  <!-- footer -->
  <div class="abs foot-brand"><div class="brand-mark"></div><div class="brand-name">VELLISANT</div></div>
  <div class="social on" style="left:276px" aria-label="Social link"></div>
  <div class="social" style="left:318px" aria-label="Social link"></div>
  <div class="social" style="left:361px" aria-label="Social link"></div>
  <div class="social" style="left:404px" aria-label="Social link"></div>
  <div class="abs copy">© <b>VELLISANT</b> - 2017. All rights reserved.</div>
</div>
</body>
</html>
```